Tsepiso Academy one-page profile

I need to develop a professionally designed "one-pager" for a new independent school opening in the Alexandra Township in South Africa in 2015. Alexandra is one of the poorest communities in South Africa and our aim is to bring a university preparatory education to this community. The school will open with kindergarten students and will expand each year until we reach grade 12. I would like for the file to be in a format that I can easily edit in the event that the information that I provide in the attachment changes or should I choose to utilize the format for an additional flyer.

The document needs to be designed as an A4 paper sized document as opposed to the standard size used in the United States.

I like the format of the following document:
http://www.brenvalelearning.org/pdfs/11.30.2012%20BRLS%20Tutoring%20One%20Pager.pdf
http://www.flintquarrypress.com/images/150_Teacher_recruitment_flyer.jpg
http://slatehollow.org/2013/01/18/BRLN%2520ODTS%2520Lottery%2520Information_English%2520Flyer%5B1%5D.jpg
Updates

I edited the attached Tsepiso Academy one page profile by altering it slightly and cutting out some unnecessary wording.  Please view to make changes.

Target Market(s)

The target market for this piece are potential funders and partners.

Industry/Entity Type

University

Requirements
Must have
• The design must use the Tsepiso Academy colors and fonts as outlined in the branding guide. The design must look professional and must give the impression of a stellar private school.
Should not have
• Clip art

```html
<!DOCTYPE html>
<html lang="en">
<head>
<meta charset="utf-8">
<title>Tsepiso Academy – One-Page Profile</title>
<link href="https://fonts.googleapis.com/css2?family=Open+Sans:wght@400;600;700&family=Roboto+Condensed:wght@700;900&display=swap" rel="stylesheet">
<style>
  :root{
    --blue:#2f80cc;
    --blue-dark:#1d5f9f;
    --blue-light:#6db8ea;
    --blue-pale:#d6eaf8;
    --ink:#4a4f55;
    --paper:#ffffff;
    --backdrop:#e8eaec;
  }
  *{box-sizing:border-box;margin:0;padding:0}
  html,body{width:1200px;height:1000px;overflow:hidden}
  body{background:var(--backdrop);font-family:"Open Sans",Arial,sans-serif;color:var(--ink);position:relative}

  .page{position:absolute;top:104px;width:560px;height:792px;background:var(--paper);overflow:hidden;box-shadow:0 4px 14px rgba(0,0,0,.18)}
  .page--back{left:30px}
  .page--front{left:610px}

  .heading{font-family:"Roboto Condensed","Arial Narrow",sans-serif;font-weight:700;color:var(--blue);font-size:12.5px;letter-spacing:.3px;text-transform:uppercase;margin-bottom:2px}
  .copy{font-size:7.8px;line-height:1.38;margin-bottom:7px}
  .copy strong{font-weight:700}

  /* photo placeholders */
  .photo{position:absolute}
  .photo--hero{left:0;top:0;width:560px;height:440px;background:linear-gradient(140deg,#f1f5f9 0%,#cfdeee 45%,#a9c3de 70%,#7a5a48 100%)}
  .collage{position:absolute;left:0;top:0;width:560px;height:440px;background:#fff}
  .photo--gray{background:linear-gradient(135deg,#d9d9d9,#8c8c8c 60%,#5e5e5e)}

  .swoosh{position:absolute;left:0;width:560px}
  .page--back .swoosh{top:340px;height:120px}
  .page--front .swoosh{top:390px;height:90px}

  /* front: brand panel */
  .brand-panel{position:absolute;left:335px;top:160px;width:205px;height:250px;background:linear-gradient(180deg,rgba(255,255,255,.95) 0%,rgba(255,255,255,.92) 55%,rgba(214,234,248,.95) 100%);padding:18px 16px 0}
  .brand{display:flex;align-items:center;gap:8px;margin-bottom:18px}
  .brand__mark{width:28px;height:28px;border-radius:50%;background:var(--blue);flex:none}
  .brand__name{font-family:"Open Sans",Arial,sans-serif;font-weight:600;color:var(--blue);font-size:15px;text-transform:uppercase;letter-spacing:.5px;line-height:1}
  .slogan{font-family:"Roboto Condensed","Arial Narrow",sans-serif;font-weight:900;color:var(--blue);font-size:46px;line-height:.95;text-transform:uppercase}

  .front-content{position:absolute;left:26px;right:26px;top:478px}
  .model{display:flex;gap:20px}
  .model ul{list-style:none;font-size:7.8px;line-height:1.4;flex:1}
  .model li::before{content:"•";color:var(--blue);margin-right:5px}

  .footer{position:absolute;left:0;bottom:0;width:560px;height:34px;background:linear-gradient(90deg,var(--blue-light),var(--blue));color:#fff;display:flex;align-items:center;font-size:9px;font-weight:600}
  .contact{display:flex;align-items:center;gap:6px;flex:1;justify-content:center}
  .contact svg{width:12px;height:12px;flex:none}
  .footer--note{font-size:8.4px;font-weight:400;padding:0 22px;justify-content:flex-start}

  /* back */
  .back-content{position:absolute;left:26px;right:26px;top:466px}
  .back-content .heading{font-size:14px}
  .back-content .copy{font-size:8.6px;line-height:1.5;margin-bottom:8px}
  .components{display:grid;grid-template-columns:1.45fr 1fr;gap:8px 18px;margin:8px 0 16px}
  .component{display:flex;align-items:center;gap:8px;font-family:"Roboto Condensed","Arial Narrow",sans-serif;font-weight:700;color:var(--blue);font-size:16px}
  .component svg{width:15px;height:15px;flex:none}
</style>
</head>
<body>

<section class="page page--back">
  <div class="collage">
    <div class="photo photo--gray" style="left:0;top:0;width:300px;height:230px" role="img" aria-label="Black and white photo of a teacher helping a young student write at a desk"></div>
    <div class="photo photo--gray" style="left:304px;top:0;width:256px;height:195px" role="img" aria-label="Black and white photo of a girl reading in a classroom"></div>
    <div class="photo photo--gray" style="left:0;top:234px;width:190px;height:206px" role="img" aria-label="Black and white photo of children working at a table"></div>
    <div class="photo photo--gray" style="left:194px;top:234px;width:106px;height:206px" role="img" aria-label="Black and white photo of a teacher with pupils"></div>
    <div class="photo photo--gray" style="left:304px;top:199px;width:256px;height:241px" role="img" aria-label="Black and white photo of a teacher reading with a child"></div>
  </div>
  <svg class="swoosh" viewBox="0 0 560 120" preserveAspectRatio="none" aria-hidden="true">
    <path d="M0 40 C160 10 330 30 560 100 L560 120 L0 120 Z" fill="#6db8ea"/>
    <path d="M0 60 C170 32 340 58 560 114 L560 120 L0 120 Z" fill="#2f80cc"/>
    <path d="M0 74 C180 48 360 80 560 120 L0 120 Z" fill="#ffffff"/>
  </svg>

  <div class="back-content">
    <h2 class="heading">Core Components</h2>
    <p class="copy">At Tsepiso Academy, we have identified four core components that will be prioritized, tracked and grown as we work towards achieving our mission of ensuring that all students are prepared with the academic and character skills that they need to be successful in university.</p>
    <div class="components">
      <div class="component"><svg viewBox="0 0 14 14"><path d="M2 2 L12 12 M12 2 L2 12" stroke="#2f80cc" stroke-width="2.2" stroke-linecap="round"/></svg>Social Justice Foundation</div>
      <div class="component"><svg viewBox="0 0 14 14"><path d="M2 2 L12 12 M12 2 L2 12" stroke="#2f80cc" stroke-width="2.2" stroke-linecap="round"/></svg>Literacy Focus</div>
      <div class="component"><svg viewBox="0 0 14 14"><path d="M1 3 H13 M7 3 V13" stroke="#2f80cc" stroke-width="2.2" stroke-linecap="round"/></svg>Standards based Unit and Lesson Planning</div>
      <div class="component"><svg viewBox="0 0 14 14"><path d="M2 2 L7 8 L12 2 M7 8 V13" stroke="#2f80cc" stroke-width="2.2" stroke-linecap="round" fill="none"/></svg>Data Driven Instruction</div>
    </div>
    <h2 class="heading">Our School Leader</h2>
    <p class="copy">Naledi Mokoena is a passionate educator and advocate for social justice. She has served as a contributing writer for education journals and, in 2012, was named a fellow for her work in urban school design, where she spoke on the importance of an education rooted in social justice. Naledi is excited about the opportunity to lead Tsepiso Academy in the community where she grew up. She began her career teaching middle school mathematics, where her students made strong gains on state assessments, and later served as an instructional coach supporting new teachers across a network of high performing schools. Before joining Tsepiso Academy, she spent two years as an operations coordinator at a growing charter network. Naledi holds an MEd degree in Education Policy and a BA in Psychology, and was a leadership fellow at a teacher residency programme.</p>
  </div>

  <footer class="footer footer--note">If you have questions, please contact a member of our team at +27 71 555 0142 or by email at info@kgotlarise.org</footer>
</section>

<section class="page page--front">
  <div class="photo photo--hero" role="img" aria-label="Photo of a smiling young boy in a light blue school shirt reading an open book"></div>

  <div class="brand-panel">
    <div class="brand">
      <span class="brand__mark"></span>
      <span class="brand__name">Tsepiso Academy</span>
    </div>
    <p class="slogan">Set Your<br>Dreams<br>Free!</p>
  </div>

  <svg class="swoosh" viewBox="0 0 560 90" preserveAspectRatio="none" aria-hidden="true">
    <path d="M0 10 C180 60 360 70 560 20 L560 90 L0 90 Z" fill="#6db8ea"/>
    <path d="M0 30 C190 75 370 80 560 40 L560 90 L0 90 Z" fill="#1d5f9f"/>
    <path d="M0 48 C200 88 380 90 560 62 L560 90 L0 90 Z" fill="#ffffff"/>
  </svg>

  <div class="front-content">
    <h2 class="heading">Who Are We</h2>
    <p class="copy">Tsepiso Academy is a grade R–12 private, university preparatory school opening in the Alexandra Township in 2015. In year one, Tsepiso Academy will serve grade R students and each year an additional grade will be added. Tsepiso Academy is a fee-paying school and all revenue is granted back to the school.<br>Tsepiso Academy is a proud member of the <strong>Open Horizon Network of Schools</strong>, an organization founded in the United States, committed to forming a global network of transformational schools.</p>

    <h2 class="heading">Our Mission</h2>
    <p class="copy">At Tsepiso Academy we grow and strengthen our academic and character skills and are prepared for success in university and beyond. We work relentlessly to develop ourselves and others and grow as leaders who will use our voices to enrich our communities.</p>

    <h2 class="heading">Our Community</h2>
    <p class="copy">Alexandra is a historic area located in the Gauteng Province in South Africa with several notable leaders residing in Alexandra at some point in their journey. Alexandra is a community full of promise; however, it is considered one of the most economically disadvantaged urban communities in the country, with a population of over 180,000 people.</p>

    <h2 class="heading">Our Model</h2>
    <p class="copy" style="margin-bottom:2px">Tsepiso Academy has several unique features designed to put all students on the path to university:</p>
    <div class="model">
      <ul>
        <li>Rigorous university preparatory curriculum</li>
        <li>Highly qualified, caring, and passionate educators</li>
        <li>Extended school day</li>
        <li>Dual language programme (English and Zulu)</li>
      </ul>
      <ul>
        <li>Creative arts and movement classes</li>
        <li>Technology integration across subject areas</li>
        <li>Extra meals built into the school day</li>
      </ul>
    </div>
  </div>

  <footer class="footer">
    <div class="contact">
      <svg viewBox="0 0 12 12"><path d="M3 1 L5 3.5 L4 5 C4.6 6.4 5.6 7.4 7 8 L8.5 7 L11 9 L10 11 C5.5 11 1 6.5 1 2 Z" fill="#fff"/></svg>
      +27 71 555 0142
    </div>
    <div class="contact">
      <svg viewBox="0 0 12 12"><circle cx="6" cy="6" r="5" fill="none" stroke="#fff" stroke-width="1.2"/><path d="M1 6 H11 M6 1 C3.5 3.5 3.5 8.5 6 11 M6 1 C8.5 3.5 8.5 8.5 6 11" fill="none" stroke="#fff" stroke-width="1"/></svg>
      www.kgotlarise.org
    </div>
    <div class="contact">
      <svg viewBox="0 0 12 12"><rect x="1" y="2.5" width="10" height="7" fill="none" stroke="#fff" stroke-width="1.2"/><path d="M1 2.5 L6 6.5 L11 2.5" fill="none" stroke="#fff" stroke-width="1.2"/></svg>
      info@kgotlarise.org
    </div>
  </footer>
</section>

</body>
</html>
```